Design a New Business Card for Our Company

We are looking for fresh, unique, and a modern business card that reflects our roots as digital marketing agency focused on SEM.

Industry/Entity Type

Marketing

Contact Information for Business Card

looking for very unique out of the box designs. clean and modern that compliments our logo

Requirements
Must have
• colors should match our logo
• Front should have name, address, email, and phone/fax of the person, phone/fax are the same number
• back should have our url

```html
<!DOCTYPE html>
<html lang="en">
<head>
<meta charset="utf-8">
<title>Tidemark Media – Business Card</title>
<link rel="stylesheet" href="https://fonts.googleapis.com/css2?family=Source+Sans+3:wght@400;600;700&display=swap">
<style>
  :root {
    --page-bg: #ececec;
    --card-white: #ffffff;
    --brand-blue: #5694d0;
    --brand-blue-dark: #3f7fbf;
    --strip-light: #d3d3d3;
    --strip-mid: #a9a9a9;
    --brand-grey: #9a9a9a;
    --back-grey: #a8a8a8;
    --text-white: #ffffff;
    --card-shadow: 0 4px 14px rgba(0,0,0,0.18);
  }
  * { box-sizing: border-box; margin: 0; padding: 0; }
  html, body { width: 940px; height: 1200px; overflow: hidden; }
  body {
    background: var(--page-bg);
    font-family: "Source Sans 3", "Myriad Pro", Arial, sans-serif;
    position: relative;
  }
  .card {
    position: absolute;
    width: 514px;
    height: 295px;
    left: 213px;
    box-shadow: var(--card-shadow);
    overflow: hidden;
  }
  .card--front { top: 150px; background: var(--card-white); }
  .card--back  { top: 720px; background: var(--back-grey); }

  /* front: brand area */
  .brand {
    position: absolute;
    left: 0; top: 0;
    width: 245px; height: 100%;
    display: flex;
    align-items: center;
    justify-content: center;
    gap: 8px;
  }
  .brand__dot {
    width: 18px; height: 18px;
    border-radius: 50%;
    background: var(--brand-blue);
    flex: none;
  }
  .brand__name {
    font-weight: 600;
    font-size: 25px;
    color: var(--brand-grey);
    letter-spacing: -0.3px;
    white-space: nowrap;
  }

  /* front: divider strip */
  .divider-line {
    position: absolute;
    left: 245px; top: 0;
    width: 3px; height: 100%;
    background: var(--brand-blue);
  }
  .strip {
    position: absolute;
    left: 249px; top: 0;
    width: 32px; height: 100%;
    background: repeating-linear-gradient(
      to bottom,
      var(--strip-light) 0 25px,
      var(--strip-mid) 25px 50px
    );
  }
  .icon-pill {
    position: absolute;
    left: 253px; top: 106px;
    width: 24px; height: 78px;
    border-radius: 12px;
    background: var(--brand-blue);
    display: flex;
    flex-direction: column;
    align-items: center;
    justify-content: space-evenly;
    padding: 4px 0;
  }
  .icon-pill svg { width: 13px; height: 13px; display: block; }

  /* front: contact panel */
  .contact {
    position: absolute;
    left: 281px; top: 0;
    width: 233px; height: 100%;
    background: var(--brand-blue);
    color: var(--text-white);
    padding: 60px 0 0 11px;
    font-size: 13.5px;
    line-height: 17.5px;
  }
  .contact__name { font-weight: 700; font-size: 16px; line-height: 19px; }
  .contact__role { margin-bottom: 17px; }
  .contact__lines { margin-bottom: 16px; }

  /* back */
  .back__circle {
    position: absolute;
    left: 60px; top: 55px;
    width: 185px; height: 185px;
    border-radius: 50%;
    background: var(--brand-blue);
  }
  .back__brand {
    position: absolute;
    right: 40px; top: 112px;
    text-align: right;
    color: var(--text-white);
  }
  .back__name { font-weight: 600; font-size: 34px; letter-spacing: -0.4px; line-height: 38px; }
  .back__url { font-size: 14px; margin-top: 6px; }
</style>
</head>
<body>

<section class="card card--front" aria-label="Business card front">
  <div class="brand">
    <span class="brand__dot"></span>
    <span class="brand__name">Tidemark Media</span>
  </div>

  <div class="divider-line"></div>
  <div class="strip"></div>
  <div class="icon-pill" aria-hidden="true">
    <svg viewBox="0 0 14 14" fill="none" stroke="#fff" stroke-width="1.3">
      <path d="M2 5c0-2 2-3 5-3s5 1 5 3l-2 1-1-2H5L4 6z" fill="#fff"/>
      <rect x="3" y="7" width="8" height="5" rx="1"/>
    </svg>
    <svg viewBox="0 0 14 14" fill="none" stroke="#fff" stroke-width="1.3">
      <rect x="4" y="2" width="6" height="4"/>
      <rect x="2" y="6" width="10" height="6" rx="1"/>
    </svg>
    <svg viewBox="0 0 14 14" fill="none" stroke="#fff" stroke-width="1.3">
      <rect x="2" y="3.5" width="10" height="7" rx="0.5"/>
      <path d="M2 4l5 4 5-4"/>
    </svg>
    <svg viewBox="0 0 14 14" fill="none" stroke="#fff" stroke-width="1.1">
      <circle cx="7" cy="7" r="5"/>
      <ellipse cx="7" cy="7" rx="2.2" ry="5"/>
      <path d="M2 7h10"/>
    </svg>
  </div>

  <div class="contact">
    <p class="contact__name">Owen Hartley</p>
    <p class="contact__role">Owner</p>
    <div class="contact__lines">
      <p>555.014.2290</p>
      <p>555.014.2290</p>
      <p>info@tidemarkmedia.com</p>
      <p>www.tidemarkmedia.com</p>
    </div>
    <p>N. 4 Cedar Row, Suite 210,</p>
    <p>Larkfield, WA 55555</p>
  </div>
</section>

<section class="card card--back" aria-label="Business card back">
  <div class="back__circle"></div>
  <div class="back__brand">
    <p class="back__name">Tidemark Media</p>
    <p class="back__url">www.tidemarkmedia.com</p>
  </div>
</section>

</body>
</html>
```